Gobal construction supply company needs new business card design

I need a business card design for my global supply company using an existing logo. i will be looking to print these on rounded corner cards with the black background version of my logo on the back. on the front white background, my logo again and my simple details.

```html
<!DOCTYPE html>
<html lang="en">
<head>
<meta charset="utf-8">
<title>Meridian Supply Works – Business Card</title>
<link rel="stylesheet" href="https://fonts.googleapis.com/css2?family=Montserrat:wght@500;600;700;800&display=swap">
<style>
  :root {
    --stage: #e6e6e6;
    --card-white: #ffffff;
    --card-black: #111111;
    --ink: #111111;
    --brand-red: #d40000;
    --emboss: #2c2c2c;
  }
  * { box-sizing: border-box; margin: 0; padding: 0; }
  html, body {
    width: 1200px; height: 1000px; overflow: hidden;
    background: var(--stage);
    font-family: "Montserrat", sans-serif;
  }
  .canvas { position: relative; width: 1200px; height: 1000px; }
  .card {
    position: absolute; left: 200px; width: 800px; height: 440px;
    border-radius: 34px; overflow: hidden;
  }
  /* Back side */
  .card-back { top: 40px; background: var(--card-black); }
  .back-wordmark {
    position: absolute; inset: 0;
    display: flex; align-items: center; justify-content: center;
  }
  .back-wordmark .brand-name {
    color: var(--emboss); font-weight: 700; font-size: 40px; letter-spacing: 2px;
    white-space: nowrap;
  }
  /* Front side */
  .card-front { top: 520px; background: var(--card-white); }
  .edge-band {
    position: absolute; left: 0; top: 0; bottom: 0; width: 62px;
    background: var(--brand-red);
  }
  .edge-rule {
    position: absolute; left: 62px; top: 0; bottom: 0; width: 8px;
    background: var(--ink);
  }
  .front-wordmark {
    position: absolute; right: 44px; top: 70px;
  }
  .front-wordmark .brand-name {
    color: var(--ink); font-weight: 800; font-size: 34px; letter-spacing: 1px;
    white-space: nowrap;
  }
  .details {
    position: absolute; left: 118px; top: 150px; color: var(--ink);
  }
  .person-name {
    color: var(--brand-red); font-weight: 700; font-size: 22px; letter-spacing: .5px;
  }
  .person-role { font-size: 15px; font-weight: 500; margin-top: 2px; }
  .address {
    margin-top: 22px; font-size: 16px; font-weight: 600; line-height: 1.3;
  }
  .contact-list { list-style: none; margin-top: 4px; }
  .contact-list li {
    display: flex; align-items: center; gap: 10px;
    font-size: 17px; font-weight: 600; line-height: 1.45;
  }
  .contact-list svg { width: 15px; height: 15px; flex: none; }
</style>
</head>
<body>
<main class="canvas">

  <section class="card card-back" aria-label="Card back">
    <div class="back-wordmark">
      <span class="brand-name">MERIDIAN SUPPLY WORKS</span>
    </div>
  </section>

  <section class="card card-front" aria-label="Card front">
    <div class="edge-band"></div>
    <div class="edge-rule"></div>

    <div class="front-wordmark">
      <span class="brand-name">MERIDIAN SUPPLY WORKS</span>
    </div>

    <div class="details">
      <p class="person-name">DANIEL MARSH</p>
      <p class="person-role">Managing Director</p>
      <p class="address">2150 Cedar Lane,<br>Tulsa, OK 74105</p>
      <ul class="contact-list">
        <li>
          <svg viewBox="0 0 16 16" aria-hidden="true"><path fill="#d40000" d="M3.5 1.5l2.5 0 1 3.5-1.6 1.2a8 8 0 0 0 4.4 4.4L11 9l3.5 1v2.5c0 1-1 2-2 2A11 11 0 0 1 1.5 3.5c0-1 1-2 2-2z"/></svg>
          +1 (555) 210 4830
        </li>
        <li>
          <svg viewBox="0 0 16 16" aria-hidden="true"><rect x="4" y="1" width="8" height="14" rx="1.5" fill="none" stroke="#d40000" stroke-width="1.8"/><circle cx="8" cy="12.3" r="1" fill="#d40000"/></svg>
          +1 (555) 210 4830
        </li>
        <li>
          <svg viewBox="0 0 16 16" aria-hidden="true"><rect x="1" y="3" width="14" height="10" rx="1.5" fill="#d40000"/><path d="M1.5 4l6.5 5 6.5-5" fill="none" stroke="#fff" stroke-width="1.4"/></svg>
          dan@meridiansw.com
        </li>
        <li>
          <svg viewBox="0 0 16 16" aria-hidden="true"><circle cx="8" cy="8" r="7" fill="#d40000"/><path d="M1 8h14M8 1c-3 3.5-3 10.5 0 14M8 1c3 3.5 3 10.5 0 14" fill="none" stroke="#fff" stroke-width="1.1"/></svg>
          www.meridiansw.com
        </li>
      </ul>
    </div>
  </section>

</main>
</body>
</html>
```